Hardcore nerd needs to stand out in a sea of dull Defence business cards

Wombarra Devices is a new Australian consulting engineering company that turns research and theory into practical systems. No evangelistic fluff, just mathematics and physics into electronic and optical circuits for consumer products, scientific research or Defence applications.

We already have a recognised logo (provided) which is often dark blue/black on a light background but we're open to other combinations. (Us engineers tend to have limited aesthetic imagination :)

Some of our recent products have included:
* Instrumentation for electrical testing,
* Radar jammers,
* GPS antenna design,
* Satellite tracking systems,
* High power lasers

We're open to both single and double-sided designs - happy to be convinced either way.

P.S. Another group is working on the web page, so - alas - our web site is currently of no use for images/ideas...

Target Market(s)

Engineering managers,
Scientists

Contact Information for Business Card

Dr Colin Harte
R&D Engineer

colin@wombarradevices.com.au
0427 563 710

PO Box XXX (to be confirmed)
Kelsby ACT 2917
Australia

Font styles to use
Serif
Sans Serif

Colors

Designer to choose colors to be used in the design.

Requirements
Must have
• My contact details!
• I've had many (great) "bold and plain" designs submitted already, so feel free to be artistically creative :)
• Happy to take advice re fonts/colours/printability etc.
Nice to have
• I'm not sure if "lists" are more at home on a CV than a business card, but representative services include:
• Applied electromagnetics
• RF and high speed electronics
• Signal and image processing
• Electro-optical and laser systems
• Concept-to-prototype design services
• If you're considering double sided cards, then often measuring/alignment grids/rulers feature on the back of similar cards.
• e.g. https://www.veltranoptics.example/newgrouppage9.cfm?objectgroup_id=4183
• https://www.veltranoptics.example/newgrouppage9.cfm?objectgroup_ID=4185
• ..or even a "Smith chart" (google will return lots)
• Generic images to represent a capability might work - googling images associated with keyword for each of these areas might help:
• - "passive radar", "phased array", "fdtd", "vircator"
• RF and high speed electronic design
• - "smith chart", "microstrip circuits", "dimensioned drawing", "electronic schematic"
• - "dft", "iir filter"
• - "optical cavity". "laser energy level diagram"
• Background/watermarked images outlines/wireframes/schematics would probably look OK.
Should not have
• If a list of projects/services is provided, it is important not to make the client feel that this is "all" the company can do. Engineering design is a creative discipline (like graphics :)
• Please, no stock "military" snaps like planes, missiles, etc!

```html
<!DOCTYPE html>
<html lang="en">
<head>
<meta charset="utf-8">
<title>Wombarra Devices – Business Card</title>
<link rel="stylesheet" href="https://fonts.googleapis.com/css2?family=EB+Garamond:wght@400;600&family=Open+Sans:wght@800&display=swap">
<style>
  :root {
    --page: #2a2b2e;
    --card: #ececec;
    --ink: #111111;
    --ink-soft: #555555;
    --band: #050505;
    --band-dark: #1c1c1f;
    --sliver: #bdbdbd;
    --rule: #444444;
  }
  * { margin: 0; padding: 0; box-sizing: border-box; }
  html, body { width: 1200px; height: 900px; overflow: hidden; background: var(--page); }
  .canvas { position: relative; width: 1200px; height: 900px; }
  .card {
    position: absolute; left: 250px; width: 700px; height: 380px;
    background: var(--card); overflow: hidden;
    font-family: "EB Garamond", Georgia, serif; color: var(--ink);
  }
  .card--front { top: 45px; }
  .card--back { top: 475px; }
  .card__band { position: absolute; inset: 0; width: 700px; height: 380px; }

  .brand { position: absolute; display: flex; align-items: center; gap: 10px; }
  .brand__dot { width: 14px; height: 14px; border-radius: 50%; background: var(--ink); }
  .brand__name { font-family: "Open Sans", Arial, sans-serif; font-weight: 800; font-size: 22px; letter-spacing: 1px; color: var(--ink); text-transform: uppercase; }

  .card--front .brand { right: 48px; top: 130px; }
  .person { position: absolute; left: 70px; top: 150px; }
  .person__name { font-size: 30px; font-weight: 600; letter-spacing: .5px; }
  .person__role { font-size: 13px; color: var(--ink-soft); margin-top: 2px; margin-left: 20px; }
  .contact { position: absolute; left: 70px; top: 238px; list-style: none; font-size: 14px; letter-spacing: 1px; color: var(--ink-soft); }
  .contact li { display: flex; align-items: center; gap: 14px; height: 30px; }
  .contact__icon { width: 22px; height: 18px; border: 1px solid #999; display: flex; align-items: center; justify-content: center; background: #f6f6f6; }

  .card--back .brand { left: 70px; top: 180px; }
  .divider-v { position: absolute; left: 400px; top: 70px; width: 1px; height: 150px; background: var(--rule); }
  .services { position: absolute; left: 425px; top: 80px; list-style: none; font-size: 15px; line-height: 26px; font-weight: 600; }
  .services li::before { content: "· "; }
  .rule-h { position: absolute; left: 400px; right: 40px; top: 232px; height: 1px; background: var(--rule); }
  .rule-h--low { left: 70px; right: 380px; top: 338px; }
  .address { position: absolute; left: 350px; top: 250px; font-size: 14px; font-weight: 600; letter-spacing: .5px; }
</style>
</head>
<body>
<main class="canvas">

  <section class="card card--front" aria-label="Card front">
    <svg class="card__band" viewBox="0 0 700 380" aria-hidden="true">
      <polygon points="370,380 400,262 700,205 700,380" fill="var(--band-dark)"/>
      <polygon points="345,380 380,250 398,250 362,380" fill="var(--sliver)"/>
      <polygon points="150,380 378,250 343,380" fill="var(--band)"/>
    </svg>
    <div class="person">
      <h1 class="person__name">Dr Colin Harte</h1>
      <p class="person__role">R&amp;D Engineer</p>
    </div>
    <ul class="contact">
      <li>
        <span class="contact__icon">
          <svg width="12" height="10" viewBox="0 0 12 10" aria-hidden="true"><path d="M1 4 Q6 0 11 4 L9 5 L8 3.5 Q6 3 4 3.5 L3 5 Z M3 6 H9 V9 H3 Z" fill="#222"/></svg>
        </span>
        colin@wombarradevices.com.au
      </li>
      <li>
        <span class="contact__icon">
          <svg width="12" height="9" viewBox="0 0 12 9" aria-hidden="true"><rect x="0.5" y="0.5" width="11" height="8" fill="#222"/><path d="M0.5 0.5 L6 5 L11.5 0.5" stroke="#f6f6f6" fill="none"/></svg>
        </span>
        0427 563 710
      </li>
    </ul>
    <div class="brand">
      <span class="brand__dot"></span>
      <span class="brand__name">Wombarra Devices</span>
    </div>
  </section>

  <section class="card card--back" aria-label="Card back">
    <svg class="card__band" viewBox="0 0 700 380" aria-hidden="true">
      <polygon points="420,380 455,292 700,250 700,380" fill="var(--band-dark)"/>
      <polygon points="398,380 435,282 452,282 414,380" fill="var(--sliver)"/>
      <polygon points="240,380 432,282 395,380" fill="var(--band)"/>
    </svg>
    <div class="brand">
      <span class="brand__dot"></span>
      <span class="brand__name">Wombarra Devices</span>
    </div>
    <div class="divider-v"></div>
    <ul class="services">
      <li>Instrumentation for electrical testing</li>
      <li>Radar jammers</li>
      <li>GPS antenna design</li>
      <li>Satellite tracking systems</li>
      <li>High power lasers</li>
    </ul>
    <div class="rule-h"></div>
    <p class="address">PO Box XXX, Kelsby ACT 2917, Australia</p>
    <div class="rule-h rule-h--low"></div>
  </section>

</main>
</body>
</html>
```